Business Card & Email Signature Design || Upmarket + Luxury

Rima Vale Honey, a New Zealand Manuka Honey company needs a Business Card & Email Signature design.

Our logo's are attached in Gold & Black versions, feel free to be creative with how you use the logo and it's patterns in your design.

Style:
- Looking for an Elegant, Luxurious, Upmarket feel.
- Black/Matte Black Card, Gold Foil, UV Embossing

Information to Add:

- Logo
- Company Name: Rima Vale Honey
- Name: Martin Holloway
- Title: Creative Director
- Phone: +64 2815 96 417
- Email: martin@rimavalehoney.example.nz
- Website: www.rimavalehoney.example.nz

- Socials: ***For email Signature Only***
- Facebook: https://www.facebook.com/rimavalehoney/
- Instagram: https://www.instagram.com/rimavalehoney/

Target Market(s)

Asia/Europe Luxury, Upmarket

Contact Information for Business Card

- Logo
- Name: Martin Holloway
- Phone: +64 2815 96 417

Font styles to use
Other font styles liked:
• Champagne & Limousines (Attached)

Requirements
Must have
• Business Card & Email Signature Design.

Looking for a Sleek, Luxury, Upmarket Design.

```html
<!DOCTYPE html>
<html lang="en">
<head>
<meta charset="UTF-8">
<title>Rima Vale Honey — Business Card</title>
<link rel="stylesheet" href="https://fonts.googleapis.com/css2?family=Montserrat:wght@300;400;500;700&display=swap">
<style>
  :root {
    --stage: #1b1b1b;
    --card: #121212;
    --card-edge: #0b0b0b;
    --gold: #d9bf78;
    --gold-deep: #8a7440;
    --pattern-dark: #16140f;
    --pattern-light: #5c4f2d;
    --ink-light: #ecebe6;
  }
  * { margin: 0; padding: 0; box-sizing: border-box; }
  html, body {
    width: 1200px; height: 780px; overflow: hidden;
    background: var(--stage);
    font-family: "Montserrat", Arial, sans-serif;
  }
  .canvas {
    position: relative; width: 1200px; height: 780px;
  }
  .card {
    position: absolute; left: 290px; width: 620px; height: 354px;
    background: var(--card);
    box-shadow: 0 10px 30px rgba(0,0,0,.55);
    overflow: hidden;
  }
  .card--back { top: 22px; }
  .card--front { top: 404px; }

  /* back side */
  .back-pattern {
    position: absolute; inset: 0;
    background: linear-gradient(120deg, var(--pattern-light) 0%, var(--pattern-dark) 62%, var(--card) 100%);
    opacity: .85;
  }
  .back-mark {
    position: absolute; right: 62px; top: 118px;
    color: var(--gold); font-size: 11px; font-weight: 500;
    letter-spacing: 2px; text-transform: uppercase;
  }

  /* front side */
  .brand {
    position: absolute; right: 56px; top: 70px;
    display: flex; align-items: center; gap: 12px;
  }
  .brand__dot {
    width: 16px; height: 16px; border-radius: 50%;
    background: var(--gold);
  }
  .brand__name {
    color: var(--gold); font-size: 27px; font-weight: 400;
    letter-spacing: 5px; text-transform: uppercase;
  }
  .divider {
    position: absolute; left: 246px; right: 26px; top: 186px;
    height: 1px; background: var(--gold-deep);
  }
  .tagline {
    position: absolute; right: 44px; top: 228px;
    color: var(--gold); font-size: 15px; font-weight: 500;
    letter-spacing: 2.5px; text-transform: uppercase;
  }
  .person {
    position: absolute; left: 34px; top: 156px;
  }
  .person__name {
    color: var(--gold); font-size: 24px; font-weight: 700;
    letter-spacing: 1px; text-transform: uppercase; line-height: 1.1;
  }
  .person__title {
    color: var(--ink-light); font-size: 15px; font-weight: 300;
    margin-top: 2px;
  }
  .contacts {
    position: absolute; left: 34px; top: 238px;
    list-style: none;
  }
  .contacts li {
    display: flex; align-items: center; gap: 14px;
    color: var(--ink-light); font-size: 14px; font-weight: 300;
    letter-spacing: .6px; height: 26px;
  }
  .contacts svg { width: 14px; height: 14px; flex: none; }
</style>
</head>
<body>
<main class="canvas">

  <section class="card card--back" aria-label="Card back">
    <div class="back-pattern" role="img" aria-label="Repeating gold foil pattern of ornamental bees fading across the card"></div>
    <span class="back-mark">Rima Vale Honey</span>
  </section>

  <section class="card card--front" aria-label="Card front">
    <div class="brand">
      <span class="brand__dot"></span>
      <span class="brand__name">Rima Vale Honey</span>
    </div>

    <div class="divider"></div>

    <div class="person">
      <h1 class="person__name">Martin Holloway</h1>
      <p class="person__title">Creative Director</p>
    </div>

    <ul class="contacts">
      <li>
        <svg viewBox="0 0 14 14" aria-hidden="true"><circle cx="7" cy="7" r="7" fill="#d9bf78"/><path d="M4.5 3.5l1.6 1.6-0.9 1.1a5 5 0 0 0 2.6 2.6l1.1-0.9 1.6 1.6-1 1a6.5 6.5 0 0 1-6-6z" fill="#121212"/></svg>
        +64 2815 96 417
      </li>
      <li>
        <svg viewBox="0 0 14 14" aria-hidden="true"><rect x="1" y="3" width="12" height="8" fill="#d9bf78"/><path d="M1 3l6 4.5L13 3" stroke="#121212" stroke-width="1" fill="none"/></svg>
        martin@rimavalehoney.example.nz
      </li>
      <li>
        <svg viewBox="0 0 14 14" aria-hidden="true"><circle cx="7" cy="7" r="6.5" fill="#d9bf78"/><ellipse cx="7" cy="7" rx="2.6" ry="6.5" stroke="#121212" stroke-width=".9" fill="none"/><path d="M0.5 7h13" stroke="#121212" stroke-width=".9"/></svg>
        www.rimavalehoney.example.nz
      </li>
    </ul>

    <p class="tagline">Rima Vale Honey</p>
  </section>

</main>
</body>
</html>
```